Corporate brochure design 4 pages

Hi,

We are a real estate company based in Europe.

We have almost finalized a rebranding.

We are developing a brand book guidelines (still on working process) to help you undertstand the look and feel of our new CI. I would like to receive proposals of design for a corporate brochure template. I need to receive the Indesign files with full ownership rights to be able to adapt all our documentation with this template.
Regarding the images, you can take gabaris on www.pelvarimages.example. I will be able to take them afterwards.

There will be 4 pages. you will receive the 4 pages on pdf for your consideration with our (almost) actual layout.

- 1st page: cover
- 2nd page: company presentation in french and english
- 3rd page: some market data + graph
- 4th page: 2 retail centers presentation.

In the template, i need to have:
- the paragraph styles in order
- 2 different masters with top/bottom/page number aso.

Please feel free to ask any other questions.

best regards,
Updates

I would like to precise tha t we are active on the commercial real estate sector:

- office transactions (rent /sales)
- property management of administrative and business buildings
- Valuation of properties
- Capital markets (investment advices for selling building)

Industry/Entity Type

Real Estate

Colors

Designer to choose colors to be used in the design.

```html
<!DOCTYPE html>
<html lang="en">
<head>
<meta charset="utf-8">
<title>Northvale – Corporate Identity & Branding Guide</title>
<link rel="stylesheet" href="https://fonts.googleapis.com/css2?family=Arimo:wght@400;700&family=Archivo+Narrow:wght@400&display=swap">
<style>
  :root {
    --stage: #e9e7e4;
    --sheet: #2a2626;
    --orange: #f26a22;
    --white: #ffffff;
    --ink: #1c1a1a;
    --copy: #e6e3e0;
    --silver-light: #f2f2f2;
    --silver-dark: #8d8f92;
  }
  html, body {
    margin: 0;
    width: 1200px;
    height: 800px;
    overflow: hidden;
    background: var(--stage);
  }
  .spread {
    position: absolute;
    left: 35px;
    top: 35px;
    width: 1132px;
    height: 730px;
    background: var(--sheet);
    overflow: hidden;
    font-family: "Arimo", Arial, sans-serif;
    color: var(--white);
  }
  .photo-frame {
    position: absolute;
    padding: 6px;
    box-sizing: border-box;
    background: linear-gradient(135deg, var(--silver-light), var(--silver-dark) 45%, var(--silver-light) 70%, var(--silver-dark));
  }
  .photo-frame--left {
    left: 0; top: 32px; width: 448px; height: 316px;
    padding-left: 0;
    border-radius: 0 26px 26px 0;
  }
  .photo-frame--right {
    left: 642px; top: 197px; width: 490px; height: 347px;
    padding-right: 0;
    border-radius: 26px 0 0 26px;
  }
  .photo {
    width: 100%;
    height: 100%;
  }
  .photo--office {
    border-radius: 0 21px 21px 0;
    background: linear-gradient(180deg, #8fb4dc 0%, #dfe6ee 30%, #d9d6cc 55%, #5d6f86 72%, #6b7a4e 86%, #3e3f42 100%);
  }
  .photo--tower {
    border-radius: 21px 0 0 21px;
    background: linear-gradient(160deg, #c9d9ea 0%, #b7cde2 35%, #4f7894 60%, #2e5670 82%, #1f3e52 100%);
  }
  .brand-tab {
    position: absolute;
    left: 872px; top: 0;
    width: 233px; height: 119px;
    background: var(--white);
    border-radius: 0 0 16px 16px;
    display: flex;
    align-items: center;
    justify-content: center;
  }
  .brand-name {
    font-family: "Arimo", Arial, sans-serif;
    font-weight: 700;
    letter-spacing: -1px;
    margin: 0;
  }
  .brand-tab .brand-name {
    font-size: 36px;
    color: var(--ink);
  }
  .intro-copy {
    position: absolute;
    left: 88px; top: 405px;
    width: 346px;
    font-family: "Archivo Narrow", "Arial Narrow", sans-serif;
    font-size: 10.6px;
    line-height: 15.4px;
    color: var(--copy);
    text-align: justify;
  }
  .intro-copy p { margin: 0 0 15px; }
  .footer-brand {
    position: absolute;
    left: 17px; top: 668px;
  }
  .footer-brand .brand-name {
    font-size: 32px;
    color: var(--white);
  }
  .contact {
    position: absolute;
    left: 206px; top: 671px;
    font-family: "Archivo Narrow", "Arial Narrow", sans-serif;
    font-size: 9px;
    line-height: 12px;
    color: var(--copy);
  }
  .contact p { margin: 0; }
  .contact .address {
    font-size: 16px;
    line-height: 20px;
    margin-top: 6px;
    color: var(--white);
  }
  .title-band {
    position: absolute;
    left: 566px; top: 607px;
    width: 505px; height: 61px;
    background: var(--orange);
    border-radius: 0 31px 31px 0;
    display: flex;
    align-items: center;
    padding-left: 16px;
    box-sizing: border-box;
  }
  .title-band h1 {
    margin: 0;
    font-size: 18.5px;
    font-weight: 700;
    letter-spacing: 0.2px;
    color: var(--white);
  }
  .web-address {
    position: absolute;
    left: 584px; top: 703px;
    font-size: 12px;
    color: var(--white);
  }
</style>
</head>
<body>
  <main class="spread">
    <div class="photo-frame photo-frame--left">
      <div class="photo photo--office" role="img" aria-label="Photo of a modern two-storey office building with glass facade, trees and a parking lot under a blue sky"></div>
    </div>

    <section class="intro-copy">
      <p>Lorem ipsum dolor sit amet, consectetur adipiscing elit. Nulla faucibus libero eu mi elementum semper. Nulla auctor sem vitae ante faucibus, et ultricies mauris ullamcorper. Nulla facilisi. Mauris vel tempor dolor, ac tempus elit. Cras id ante molestie, vehicula lorem quis, bibendum magna. Nunc euismod velit eu turpis interdum, lacinia dictum lorem scelerisque. Cras lectus nisi, venenatis eget dolor id, dignissim blandit lorem.</p>
      <p>Integer aliquet pellentesque euismod. Nunc eleifend, urna in congue pulvinar, magna ante consectetur arcu, non gravida justo metus eu velit. Ut feugiat orci a eros feugiat, eu condimentum tortor volutpat. Aliquam ut metus porttitor, tristique enim id, suscipit sapien. Donec rutrum ipsum est, eu ultricies turpis condimentum vel. Nulla elementum augue imperdiet velit sagittis, ac eleifend quam consequat. Etiam fringilla tortor et dictum ultricies. Nunc eget velit tincidunt, tincidunt est porta, euismod erat. Mauris ultricies commodo orci, sed vulputate metus blandit vitae. Integer consequat euismod pretium. Sed at eros arcu</p>
    </section>

    <div class="footer-brand">
      <p class="brand-name">NORTHVALE</p>
    </div>

    <address class="contact">
      <p>Ph. 000-XXX-XXXX-000 | Fax. 000-XXX-XXXX-000</p>
      <p>Email . email@website.com | web. www.website.com</p>
      <p class="address">Put Your Address</p>
    </address>

    <div class="brand-tab">
      <p class="brand-name">NORTHVALE</p>
    </div>

    <div class="photo-frame photo-frame--right">
      <div class="photo photo--tower" role="img" aria-label="Photo looking up at a curved glass office tower with a slatted roof canopy against a pale sky"></div>
    </div>

    <div class="title-band">
      <h1>2014 CORPORATE IDENTITY &amp; BRANDING GUIDE</h1>
    </div>

    <p class="web-address">www.northvale-re.example</p>
  </main>
</body>
</html>
```